Corvel Capital LLC

Need Professional Business cards for New Investment Fund

Target Market(s)

High Quality investors

Industry/Entity Type

Financial

Contact Information for Business Card

Phone Number +1 555 284 6190
Name Lukas Varenko
Title Fund Manager
email lv@FundCorvel.com
Website www.FundCorvel.com

Colors

Designer to choose colors to be used in the design.

Requirements
Must have
• Must have our Logo and all of the above. Must be made so lettering and loge can be raised

```html
<!DOCTYPE html>
<html lang="en">
<head>
<meta charset="utf-8">
<title>Quorvane – Business Card</title>
<link rel="stylesheet" href="https://fonts.googleapis.com/css2?family=Lato:wght@400;700&display=swap">
<style>
  :root {
    --bg: #2f2f2f;
    --paper: #ffffff;
    --green: #1fdd0c;
    --green-deep: #2c8a24;
    --moss: #3a4a3c;
    --ink: #3b4a3d;
    --ink-soft: #5a5f5a;
    --white: #ffffff;
  }
  * { box-sizing: border-box; margin: 0; padding: 0; }
  html, body { width: 1200px; height: 866px; overflow: hidden; }
  body {
    background: var(--bg);
    font-family: "Lato", sans-serif;
    display: flex;
    align-items: center;
    justify-content: center;
    gap: 40px;
  }
  .card {
    position: relative;
    width: 540px;
    height: 309px;
    overflow: hidden;
    box-shadow: 0 10px 24px rgba(0,0,0,.45);
  }

  /* front */
  .card--front { background: var(--paper); }
  .card__edge {
    position: absolute; left: 0; right: 0; bottom: 0; height: 7px;
    background: linear-gradient(90deg, var(--green) 0 36%, var(--moss) 36% 100%);
  }
  .holder { position: absolute; left: 36px; top: 84px; }
  .holder__name {
    font-weight: 700; font-size: 24px; letter-spacing: .5px; line-height: 28px;
    text-transform: uppercase; color: var(--ink); white-space: nowrap;
  }
  .holder__first { color: var(--green); }
  .holder__title { font-size: 16px; color: var(--ink-soft); margin-top: 2px; }
  .contacts { list-style: none; margin-top: 16px; }
  .contacts__item {
    display: flex; align-items: center; gap: 8px;
    font-size: 15px; color: var(--ink); line-height: 22px; white-space: nowrap;
  }
  .contacts__icon { width: 12px; height: 12px; fill: var(--green); flex: none; }

  .brand { display: flex; align-items: center; gap: 10px; }
  .brand__mark { width: 18px; height: 18px; background: var(--green); flex: none; }
  .brand__name {
    font-weight: 700; font-size: 26px; letter-spacing: 2px;
    text-transform: uppercase; color: var(--ink); white-space: nowrap;
  }
  .card--front .brand { position: absolute; right: 36px; top: 196px; }

  /* back */
  .card--back {
    background: linear-gradient(35deg, var(--moss) 0%, var(--green-deep) 45%, var(--green) 100%);
    display: flex; align-items: center; justify-content: center;
  }
  .card--back .brand__mark { background: var(--white); }
  .card--back .brand__name { color: var(--white); font-size: 30px; }
</style>
</head>
<body>
  <section class="card card--front" aria-label="Card front">
    <div class="holder">
      <h1 class="holder__name"><span class="holder__first">Lukas</span> Varenko</h1>
      <p class="holder__title">Fund Manager</p>
      <ul class="contacts">
        <li class="contacts__item">
          <svg class="contacts__icon" viewBox="0 0 12 12" aria-hidden="true"><path d="M2.5 1l2 2.2-1 1.3c.7 1.5 1.6 2.4 3 3l1.3-1L10 8.5 9 11C4.5 10.5 1.5 7.5 1 3z"/></svg>
          +1 555 284 6190
        </li>
        <li class="contacts__item">
          <svg class="contacts__icon" viewBox="0 0 12 12" aria-hidden="true"><path d="M0 2h12v8H0z M1 3l5 3.5L11 3v-.2H1z" fill-rule="evenodd"/></svg>
          lv@FundCorvel.com
        </li>
        <li class="contacts__item">
          <svg class="contacts__icon" viewBox="0 0 12 12" aria-hidden="true"><path d="M6 0a4 4 0 0 1 4 4c0 3-4 8-4 8S2 7 2 4a4 4 0 0 1 4-4zm0 2.5a1.5 1.5 0 1 0 0 3 1.5 1.5 0 0 0 0-3z" fill-rule="evenodd"/></svg>
          www.FundCorvel.com
        </li>
      </ul>
    </div>
    <div class="brand">
      <span class="brand__mark"></span>
      <span class="brand__name">Quorvane</span>
    </div>
    <div class="card__edge"></div>
  </section>

  <section class="card card--back" aria-label="Card back">
    <div class="brand">
      <span class="brand__mark"></span>
      <span class="brand__name">Quorvane</span>
    </div>
  </section>
</body>
</html>
```